New, modern business card for growing audiology practice

We need a new business card for our audiology practice. Our logo and website have recently changed (more modern) and we want our business cards to reflect this change.
We conduct hearing tests, perform earwax removals, and fit & dispense hearing aids to our patients. We are a family owned practice in which the owner is the one who works directly with the patient. I have attached logos in various formats to use, as well as two ideas I found on this website; as well as a scanned copy of our current logo. Good luck!

Industry/Entity Type

Business

Contact Information for Business Card

Company name: Tolvera Hearing Center
Provider name: Peter Wolstenby, Au.D. F/NSB
Phone number: (608) 683-5127
Address: 837 W. Lindell Ave. Brookmere Falls, WI 53907
email: tolverahearing@postvane.com
website: tolverahearing.com

Colors
000000
aaaaaa
dbdbdb
cacaca
9bcb3c
afd23c
cadf82
b1b1b1

Requirements
Must have
• My card must include information in the "details" section. In the attached images, I found a few that I liked and I would like to model after - "brisky bouncin'" and "Sound Method Center".
• Must be horizontal.
• Must include logos provided. I uploaded them in various file formats and various ways.
• Must match logo font, if possible, if not, please get as close as you can.
Nice to have
• I really like the idea of having a color on one side with just the logo and company name and the contact information and provider name on the other side. I also really like the idea of having the main color dominating on the logo/company side with accent of that same color on the contact side of the card.
Should not have
• Must not be vertical.

```html
<!DOCTYPE html>
<html lang="en">
<head>
<meta charset="utf-8">
<title>Tolvera Hearing Center – Business Card</title>
<link rel="stylesheet" href="https://fonts.googleapis.com/css2?family=Lato:wght@400;700&family=Source+Sans+3:wght@400;600;700&display=swap">
<style>
  :root {
    --black: #000000;
    --white: #ffffff;
    --green: #7aab3e;
    --grey-mid: #aaaaaa;
    --stage: #e9e9e6;
  }
  * { box-sizing: border-box; margin: 0; padding: 0; }
  html, body { width: 1200px; height: 900px; overflow: hidden; }
  body { background: var(--stage); position: relative; font-family: "Source Sans 3", sans-serif; }

  .card { position: absolute; overflow: hidden; box-shadow: 0 6px 18px rgba(0,0,0,.18); }

  /* Front side */
  .card--front { left: 178px; top: 75px; width: 590px; height: 365px; background: var(--white); }
  .card__shapes { position: absolute; inset: 0; }
  .brand { position: absolute; display: flex; align-items: center; gap: 14px; white-space: nowrap; }
  .brand__dot { width: 26px; height: 26px; border-radius: 50%; background: var(--green); flex: none; }
  .brand__name { font-family: "Lato", sans-serif; font-weight: 400; letter-spacing: .5px; }
  .card--front .brand { left: 66px; top: 70px; }
  .card--front .brand__name { font-size: 30px; color: var(--black); }

  .provider { position: absolute; left: 0; right: 0; top: 226px; text-align: center; color: var(--white); font-size: 16px; padding-left: 60px; }
  .provider__name { color: var(--green); font-weight: 700; font-size: 20px; letter-spacing: .5px; }

  .address { position: absolute; right: 316px; top: 280px; text-align: right; color: var(--white); font-size: 16px; line-height: 22px; font-style: normal; white-space: nowrap; }
  .divider { position: absolute; left: 293px; top: 272px; width: 1px; height: 60px; background: var(--grey-mid); }
  .contact { position: absolute; left: 314px; top: 268px; list-style: none; color: var(--white); font-size: 16px; line-height: 22px; }
  .contact li { display: flex; align-items: center; gap: 6px; }
  .contact svg { width: 13px; height: 13px; fill: var(--green); flex: none; }

  /* Back side */
  .card--back { left: 388px; top: 505px; width: 567px; height: 350px; background: var(--black); }
  .card--back .brand { left: 50%; top: 160px; transform: translateX(-50%); }
  .card--back .brand__name { font-size: 29px; color: var(--white); }
</style>
</head>
<body>

<section class="card card--front" aria-label="Business card front">
  <svg class="card__shapes" width="590" height="365" viewBox="0 0 590 365" aria-hidden="true">
    <polygon points="0,178 404,178 384,203 0,203" fill="var(--green)"/>
    <polygon points="416,168 590,168 590,365 0,365 0,208 388,208" fill="var(--black)"/>
  </svg>

  <div class="brand">
    <span class="brand__dot"></span>
    <span class="brand__name">TOLVERA HEARING CENTER</span>
  </div>

  <p class="provider"><span class="provider__name">PETER WOLSTENBY</span>, AU.D. F/NSB</p>

  <address class="address">837 W. Lindell<br>Ave. Brookmere Falls, WI 53907</address>
  <span class="divider"></span>
  <ul class="contact">
    <li><svg viewBox="0 0 24 24"><path d="M6.6 10.8a15 15 0 0 0 6.6 6.6l2.2-2.2c.3-.3.7-.4 1-.2 1.1.4 2.3.6 3.6.6.6 0 1 .4 1 1V20c0 .6-.4 1-1 1A17 17 0 0 1 3 4c0-.6.4-1 1-1h3.5c.6 0 1 .4 1 1 0 1.3.2 2.5.6 3.6.1.3 0 .7-.2 1z"/></svg>(608) 683-5127</li>
    <li><svg viewBox="0 0 24 24"><path d="M2 5h20v14H2z"/></svg>tolverahearing@postvane.com</li>
    <li><svg viewBox="0 0 24 24"><circle cx="12" cy="12" r="10"/></svg>www.tolverahearing.com</li>
  </ul>
</section>

<section class="card card--back" aria-label="Business card back">
  <div class="brand">
    <span class="brand__name">TOLVERA HEARING CENTER</span>
  </div>
</section>

</body>
</html>
```